RESIDENTIAL CONSTRUCTION

We are a company that specializes in building custom residential homes, the design should also emphasize that quality and service is our priority.

Industry/Entity Type

Construction Company

Contact Information for Business Card

Contact Person: Marcus Lindqvist
Company Address: 273 West Alder Ave San Jose , Ca 95380
Phone Number : 408-731-2946
Email Address: Stoneridgehomes517@mailvista.net

Font styles to use
Sans Serif

Colors
ec1f27

Requirements
Must have
• CSLB # 7362015
Nice to have
• needs to have same color as logo i uploaded, we will be printing these on a clear plastic card.

```html
<!DOCTYPE html>
<html lang="en">
<head>
<meta charset="utf-8">
<title>Stoneridge General Builders – Business Card</title>
<link href="https://fonts.googleapis.com/css2?family=Bebas+Neue&family=Open+Sans:wght@400;600&display=swap" rel="stylesheet">
<style>
  :root {
    --backdrop: #2b2b2d;
    --card-dark: #141415;
    --card-light: #ffffff;
    --brand-red: #ec1f27;
    --brand-rose: #d9566a;
    --ink: #1a1a1a;
    --ink-soft: #3a3a3a;
    --ghost: #ededed;
  }
  * { margin: 0; padding: 0; box-sizing: border-box; }
  html, body {
    width: 1200px; height: 716px; overflow: hidden;
    background: var(--backdrop);
  }
  .stage {
    width: 1200px; height: 716px;
    display: flex; align-items: center; justify-content: center; gap: 60px;
  }
  .card {
    width: 520px; height: 300px; border-radius: 22px;
    position: relative; overflow: hidden; flex: none;
    box-shadow: 0 12px 30px rgba(0,0,0,.45);
  }
  .card--front {
    background: var(--card-dark);
    display: flex; align-items: center; justify-content: center;
  }
  .company-name {
    font-family: "Bebas Neue", sans-serif;
    font-size: 38px; line-height: 1; letter-spacing: 1.5px;
    color: var(--brand-rose);
    display: flex; align-items: center; gap: 12px;
    white-space: nowrap;
  }
  .company-name__mark {
    width: 16px; height: 16px; background: var(--brand-rose); flex: none;
  }
  .card--back { background: var(--card-light); }
  .identity {
    position: absolute; left: 16px; top: 112px;
    width: 206px; text-align: right;
  }
  .identity__name {
    font-family: "Bebas Neue", sans-serif; font-weight: 400;
    font-size: 31px; line-height: 1; color: var(--ink); letter-spacing: .3px;
    white-space: nowrap;
  }
  .identity__role {
    font-family: "Bebas Neue", sans-serif;
    font-size: 16px; line-height: 1.1; color: var(--brand-red); letter-spacing: .6px;
    margin-top: 3px; white-space: nowrap;
  }
  .divider {
    position: absolute; left: 232px; top: 108px;
    width: 2px; height: 68px; background: var(--brand-rose);
  }
  .contacts {
    position: absolute; left: 244px; top: 109px;
    list-style: none;
    font-family: "Open Sans", sans-serif; font-size: 11px; color: var(--ink-soft);
  }
  .contacts li {
    display: flex; align-items: center; gap: 7px; height: 22px; white-space: nowrap;
  }
  .contacts svg { width: 10px; height: 10px; fill: var(--brand-rose); flex: none; }
  .decor-ghost {
    position: absolute; right: 22px; bottom: 16px;
    width: 160px; height: 82px;
    background: linear-gradient(135deg, #f6f6f6, var(--ghost));
    border-radius: 6px;
  }
</style>
</head>
<body>
<main class="stage">
  <section class="card card--front">
    <div class="company-name"><span class="company-name__mark"></span>Stoneridge General Builders</div>
  </section>

  <section class="card card--back">
    <div class="identity">
      <h1 class="identity__name">Marcus Lindqvist</h1>
      <p class="identity__role">Job Title | CSLB # 7362015</p>
    </div>
    <div class="divider"></div>
    <ul class="contacts">
      <li>
        <svg viewBox="0 0 24 24"><path d="M6.6 10.8a15 15 0 0 0 6.6 6.6l2.2-2.2c.3-.3.7-.4 1-.2 1.1.4 2.3.6 3.6.6.6 0 1 .4 1 1V20c0 .6-.4 1-1 1A17 17 0 0 1 3 4c0-.6.4-1 1-1h3.5c.6 0 1 .4 1 1 0 1.3.2 2.5.6 3.6.1.3 0 .7-.2 1z"/></svg>
        408-731-2946
      </li>
      <li>
        <svg viewBox="0 0 24 24"><path d="M2 5h20v14H2z M2 5l10 8 10-8"/></svg>
        Stoneridgehomes517@mailvista.net
      </li>
      <li>
        <svg viewBox="0 0 24 24"><path d="M12 2a7 7 0 0 0-7 7c0 5.2 7 13 7 13s7-7.8 7-13a7 7 0 0 0-7-7zm0 9.5A2.5 2.5 0 1 1 12 6.5a2.5 2.5 0 0 1 0 5z"/></svg>
        273 West Alder Ave San Jose , Ca 95380
      </li>
    </ul>
    <div class="decor-ghost" role="img" aria-label="Faint ruler and house decoration"></div>
  </section>
</main>
</body>
</html>
```